Mortgage Company ready to make a statement!

We have a basic logo that I am fairly happy with ... but it could use a little bit of tweaking before we order the sign for our building. We also want some knock-your-socks-off business cards.
Problem: Inside of our Mortgage Office (Bright Fern Mortgage Group), we are going to have a coffee lounge (Sunbrew Cafe) for Realtors to use instead of the local Cuppington to meet with homebuyers. The office and coffee lounge are in an industrial building and is decorated with cozy overstuffed chairs, a hodge podge of interesting lamps and furniture, and goal is to make it as inviting as possible. However, we are a financial institution... so we need to keep it pretty clean as well.
One of my favorite marketing ideas is to cut a house key for everyone who buys a home using us with a key that matches our logo. There's only one key shape that works really well, so that needs to match the logo in order for the idea to work. I'll attach an image of the key blank.... although the way the key hole cut out looks terrible, so I was thinking of having them just do a thin outline instead.
Would like a similar, matching logo for the Sunbrew Cafe... but possibly something that would be a little less formal and would be cute on a coffee mug- nothing stuffy.
AND, we're opening a home inspection company as well, and we would like that logo and branding to match. The home inspection company is "Bright Fern Home Inspections"
We were thinking that for the home inspection company , we could use a magnifying glass shape inside of the house shape for the logo, use a keyhole shape inside of the same house for the mortgage company, and use a coffee cup inside of the house shape for Sunbrew Cafe.
Just getting stuck and need to help. I designed the attached logo myself, and that is what we are currently using. Designers at local printing companies have failed to impress us.
The mortgage industry has a lot of numbers and logos, etc that they require us to put on our business cards... so it's hard to keep them looking clean.
HELP! HELP! :)

```html
<!DOCTYPE html>
<html lang="en">
<head>
<meta charset="utf-8">
<title>Bright Fern Mortgage Group – Business Card</title>
<link href="https://fonts.googleapis.com/css2?family=Crimson+Pro:wght@500;600&family=Open+Sans:wght@400&display=swap" rel="stylesheet">
<style>
  :root {
    --backdrop: #e4e2df;
    --card-paper: #f2efec;
    --brand-blue: #22668a;
    --panel-edge: #4f5660;
    --ink: #2b2b2b;
    --paper-text: #ffffff;
  }
  * { margin: 0; padding: 0; box-sizing: border-box; }
  html, body {
    width: 1200px;
    height: 900px;
    overflow: hidden;
    background: var(--backdrop);
  }
  .card {
    position: absolute;
    left: 100px;
    top: 140px;
    width: 1000px;
    height: 620px;
    background: var(--card-paper);
    overflow: hidden;
    box-shadow: 0 6px 24px rgba(0,0,0,0.12);
  }
  .brand-name {
    position: absolute;
    left: 60px;
    top: 110px;
    font-family: "Crimson Pro", serif;
    font-weight: 500;
    font-size: 44px;
    line-height: 1.1;
    color: var(--brand-blue);
    width: 420px;
  }
  .address-panel {
    position: absolute;
    left: 509px;
    top: 150px;
    right: -8px;
    bottom: -8px;
    background: var(--brand-blue);
    border: 7px solid var(--panel-edge);
  }
  .bottom-band {
    position: absolute;
    left: 0;
    right: 0;
    bottom: 0;
    height: 50px;
    background: var(--brand-blue);
  }
  .person {
    position: absolute;
    left: 60px;
    top: 320px;
  }
  .person-name {
    font-family: "Crimson Pro", serif;
    font-weight: 600;
    font-size: 33px;
    letter-spacing: 1.5px;
    color: var(--brand-blue);
    text-transform: uppercase;
    line-height: 1.1;
  }
  .person-role {
    font-family: "Open Sans", sans-serif;
    font-size: 25px;
    color: var(--ink);
    margin-top: 4px;
  }
  .contact-list {
    position: absolute;
    left: 60px;
    top: 430px;
    list-style: none;
    font-family: "Open Sans", sans-serif;
    font-size: 25px;
    color: var(--ink);
  }
  .contact-item {
    display: flex;
    align-items: center;
    height: 37px;
  }
  .contact-icon {
    width: 18px;
    height: 18px;
    margin-right: 13px;
    fill: var(--brand-blue);
  }
  .office-address {
    position: absolute;
    right: 70px;
    top: 440px;
    text-align: right;
    font-family: "Open Sans", sans-serif;
    font-size: 25px;
    line-height: 37px;
    color: var(--paper-text);
  }
</style>
</head>
<body>
  <main class="card">
    <div class="brand-name">Bright Fern<br>Mortgage Group</div>

    <div class="address-panel"></div>
    <div class="bottom-band"></div>

    <section class="person">
      <h1 class="person-name">Daniel Whitmore</h1>
      <p class="person-role">Managing Director</p>
    </section>

    <ul class="contact-list">
      <li class="contact-item">
        <svg class="contact-icon" viewBox="0 0 24 24" aria-hidden="true"><path d="M6.6 10.8a15.1 15.1 0 0 0 6.6 6.6l2.2-2.2a1 1 0 0 1 1-.25 11.4 11.4 0 0 0 3.6.57 1 1 0 0 1 1 1V20a1 1 0 0 1-1 1A17 17 0 0 1 3 4a1 1 0 0 1 1-1h3.5a1 1 0 0 1 1 1c0 1.25.2 2.45.57 3.57a1 1 0 0 1-.25 1z"/></svg>
        (044)987654321
      </li>
      <li class="contact-item">
        <svg class="contact-icon" viewBox="0 0 24 24" aria-hidden="true"><path d="M2 5h20v14H2z M3.5 6.5 12 12.5l8.5-6" fill="var(--brand-blue)"/><path d="M3.5 6.5 12 12.5l8.5-6" fill="none" stroke="#f2efec" stroke-width="1.6"/></svg>
        info@brightfernmg.com
      </li>
      <li class="contact-item">
        <svg class="contact-icon" viewBox="0 0 24 24" aria-hidden="true"><circle cx="12" cy="12" r="10"/><path d="M2 12h20M12 2c3 3 3 17 0 20M12 2c-3 3-3 17 0 20" fill="none" stroke="#f2efec" stroke-width="1.4"/></svg>
        www.brightfernmg.com
      </li>
    </ul>

    <address class="office-address" style="font-style:normal">
      1234, Address GoesHere,<br>
      Country name, 12345
    </address>
  </main>
</body>
</html>
```